Coastal Learner Bureau business cards

Australian company about to start offering its services. We recruit international students to come to study English, vocational education and postgraduate courses in Australia. We help them find the institution and select the right city they want to come to Australia. We are a young, online oriented and supportive agency. Our clients are between 18 and 35 years old, mainly University students, young professionals or people with work experience. We provide much more information that any other agency offer. We administrate a Facebook group with more than 11.000 members that daily ask questions about general information when coming to Australia, while they are here and even after they leave the country

Target Market(s)

International students from South America, Central America and Europe

Industry/Entity Type

Student

Contact Information for Business Card

Tomas Bilbrea
Managing Director
tomas@kelvarin.com.au
www.kelvoria.com.au
+61 491058264
Melbourne, Australia

Font styles to use
Serif
Sans Serif

Colors

Designer to choose colors to be used in the design.

Requirements
Must have
• Horizontal design
• Standard business card size and shape. If font uses green or yellow colours, they will have to match the ones from the logo
Nice to have
• UPDATE: Use the contents of the green image to design one of the card sides. Use our logo in the background of that side as watermark.
• Passport image, or immigration stamps. A picture of the Yarra River (from Melbourne) would be cool as well.
Should not have
• Non-standard business card size and shape
• Not black as the background colour of any sides as we are not a VIP agency or a hight class service. We are orientes to young people and they like colours, pictures, something attractive.
• Vertical design
• NO YELLOW or BLACK AS THE BACKGROUND COLOUR OF ANY SIDE OF THE BIZ CARD

```html
<!DOCTYPE html>
<html lang="en">
<head>
<meta charset="utf-8">
<title>Coastal Learner Bureau business cards</title>
<link rel="stylesheet" href="https://fonts.googleapis.com/css2?family=Roboto:wght@400;500;700&family=Roboto+Condensed:wght@500&display=swap">
<style>
  :root {
    --backdrop: #2b2b2b;
    --paper: #f2f2f2;
    --green: #115c3a;
    --gold: #dcb50f;
    --gold-text: #d8ae12;
    --white: #ffffff;
  }
  html, body {
    margin: 0;
    padding: 0;
    width: 1200px;
    height: 960px;
    overflow: hidden;
    background: var(--backdrop);
    font-family: "Roboto", Arial, sans-serif;
  }
  .stage {
    position: relative;
    width: 1200px;
    height: 960px;
  }
  .card {
    position: absolute;
    width: 600px;
    height: 342px;
    overflow: hidden;
    box-shadow: 0 3px 6px rgba(0,0,0,0.45);
  }
  .card--front { left: 314px; top: 113px; background: var(--paper); }
  .card--back  { left: 311px; top: 472px; background: var(--green); }

  .wave { position: absolute; left: 0; top: 0; width: 600px; height: 342px; }

  .brand {
    position: absolute;
    left: 0;
    width: 100%;
    text-align: center;
    font-family: "Roboto", Arial, sans-serif;
    font-weight: 700;
    letter-spacing: 0.5px;
  }
  .card--front .brand { top: 82px; font-size: 44px; color: var(--green); }
  .card--back .brand  { top: 138px; font-size: 64px; color: var(--white); }

  .details {
    position: absolute;
    left: 0;
    top: 257px;
    width: 100%;
    text-align: center;
    color: var(--white);
  }
  .details__headline { margin: 0; line-height: 28px; }
  .details__name {
    font-family: "Roboto Condensed", "Arial Narrow", sans-serif;
    font-weight: 500;
    font-size: 22px;
    color: var(--gold-text);
  }
  .details__dash { font-size: 19px; color: var(--gold-text); margin: 0 10px; font-weight: 700; }
  .details__role { font-size: 16px; font-weight: 500; }
  .details__contact { margin: 1px 0 0; font-size: 15px; line-height: 19px; }
  .details__web { margin: 1px 0 0; font-size: 15px; font-weight: 700; color: var(--gold-text); line-height: 19px; }

  .tagline {
    position: absolute;
    left: 80px;
    top: 299px;
    width: 440px;
    display: flex;
    align-items: center;
    gap: 4px;
    color: var(--white);
    font-size: 14px;
  }
  .tagline__rule { flex: 1; height: 1px; }
  .tagline__rule--left  { background: linear-gradient(to right, rgba(255,255,255,0), rgba(255,255,255,0.9)); }
  .tagline__rule--right { background: linear-gradient(to left, rgba(255,255,255,0), rgba(255,255,255,0.9)); }
</style>
</head>
<body>
<main class="stage">
  <section class="card card--front" aria-label="Card front">
    <svg class="wave" viewBox="0 0 600 342" aria-hidden="true">
      <path d="M0,236 C150,206 300,222 420,225 C500,227 560,208 600,190 L600,342 L0,342 Z" fill="var(--green)"/>
      <path d="M2,230 C120,200 250,204 380,212 C470,217 540,204 592,186 C545,210 470,228 380,228 C260,228 150,216 2,230 Z" fill="var(--gold)"/>
    </svg>
    <div class="brand">Kelvoria</div>
    <div class="details">
      <p class="details__headline">
        <span class="details__name">TOMAS BILBREA</span><span class="details__dash">-</span><span class="details__role">MANAGING DIRECTOR</span>
      </p>
      <p class="details__contact">Melbourne, Australia | +61 491058264 | tomas@kelvarin.com.au</p>
      <p class="details__web">www.kelvoria.com.au</p>
    </div>
  </section>

  <section class="card card--back" aria-label="Card back">
    <div class="brand">Kelvoria</div>
    <div class="tagline">
      <span class="tagline__rule tagline__rule--left"></span>
      <span class="tagline__text">Hacemos más por ti!</span>
      <span class="tagline__rule tagline__rule--right"></span>
    </div>
  </section>
</main>
</body>
</html>
```